Business Card for Professional Photographer

I'm looking for an eye catching modern clean design that compliments my logo/ website fonts & colours.
I specialise in architecture, corporate & commercial photography so I'm marketing to professional clients rather than portrait / wedding clients.

I would prefer to not have a solid black design.

My logo brand guide is as follows :

Main front font. : Reislust
Main font colour : #fff
Slogan front font : Ubuntu Bold
Monogram front font : Venti Medium
Container colour : #fff

I need print ready files in pdf .png & .eps formats.

Included in the files below are some screen grabs as reference to font & colours etc.

```html
<!DOCTYPE html>
<html lang="en">
<head>
<meta charset="utf-8">
<title>Lumen Frame — Business Card</title>
<link href="https://fonts.googleapis.com/css2?family=Ubuntu:wght@300;500;700&family=Roboto:wght@400&family=Saira+Condensed:wght@600&display=swap" rel="stylesheet">
<style>
  :root {
    --backdrop: #c2c2c2;
    --card-dark: #101112;
    --card-light: #f3f3f2;
    --gold: #c9a45a;
    --gold-deep: #9a7634;
    --gold-light: #e2c47f;
    --ink: #2b2b2b;
    --ink-soft: #3a3a3a;
  }
  * { margin: 0; padding: 0; box-sizing: border-box; }
  html, body { width: 1200px; height: 576px; overflow: hidden; background: var(--backdrop); }
  .canvas { position: relative; width: 1200px; height: 576px; }

  .card {
    position: absolute; top: 138px; width: 484px; height: 294px;
    border-radius: 10px; overflow: hidden;
  }
  .card--front { left: 82px; background: var(--card-dark); }
  .card--back { left: 602px; background: linear-gradient(160deg, #fafafa 0%, var(--card-light) 60%, #e9e9e8 100%); }

  .photo-collage {
    position: absolute; inset: 0;
    background: linear-gradient(120deg, #16171a 0%, #23211f 40%, #1a1c20 70%, #111214 100%);
  }

  .wordmark { position: absolute; display: flex; align-items: center; }
  .wordmark__mark {
    border: 3px solid var(--gold); border-radius: 50%;
  }
  .wordmark__text { display: flex; flex-direction: column; }
  .wordmark__name {
    font-family: "Ubuntu", sans-serif; font-weight: 300;
    color: var(--gold); text-transform: uppercase; line-height: 1;
  }
  .wordmark__tagline {
    font-family: "Ubuntu", sans-serif; font-weight: 700;
    color: var(--gold-deep); line-height: 1;
  }

  .card--front .wordmark { left: 82px; top: 95px; }
  .card--front .wordmark__mark { width: 66px; height: 66px; margin-right: 34px; }
  .card--front .wordmark__name { font-size: 24px; letter-spacing: 3px; }
  .card--front .wordmark__tagline { font-size: 7.5px; letter-spacing: 2.2px; margin-top: 8px; color: var(--gold); }

  .front-url {
    position: absolute; left: 138px; top: 257px;
    font-family: "Ubuntu", sans-serif; font-weight: 300; font-size: 13px;
    letter-spacing: 1.6px; color: var(--gold-light);
  }

  .card--back .wordmark { left: 30px; top: 46px; }
  .card--back .wordmark__mark { width: 64px; height: 64px; margin-right: 28px; }
  .card--back .wordmark__name { font-size: 22px; letter-spacing: 3px; }
  .card--back .wordmark__tagline { font-size: 7.5px; letter-spacing: 2px; margin-top: 8px; }

  .person { position: absolute; left: 29px; top: 176px; }
  .person__name {
    font-family: "Saira Condensed", sans-serif; font-weight: 600;
    font-size: 20px; color: var(--gold-deep); line-height: 1;
  }
  .person__role {
    font-family: "Roboto", sans-serif; font-size: 12.5px; color: var(--ink-soft); margin-top: 4px;
  }

  .contact-list { position: absolute; left: 252px; top: 172px; list-style: none; }
  .contact-list li {
    display: flex; align-items: center; height: 18px;
    font-family: "Roboto", sans-serif; font-size: 12.5px; color: var(--ink);
  }
  .contact-list svg { width: 10px; height: 10px; margin-right: 10px; fill: var(--gold); }

  .gold-band { position: absolute; left: 0; bottom: 0; width: 484px; height: 40px; }
  .address {
    position: absolute; right: 38px; bottom: 14px;
    font-family: "Roboto", sans-serif; font-size: 12.5px; color: var(--ink);
  }
</style>
</head>
<body>
<div class="canvas">

  <section class="card card--front">
    <div class="photo-collage" role="img" aria-label="Darkened collage of architecture, interior and commercial photographs"></div>
    <div class="wordmark">
      <span class="wordmark__mark"></span>
      <div class="wordmark__text">
        <span class="wordmark__name">Lumen Frame</span>
        <span class="wordmark__tagline">Architecture Corporate Commercial</span>
      </div>
    </div>
    <p class="front-url">www.lumenframe.com.au</p>
  </section>

  <section class="card card--back">
    <div class="wordmark">
      <span class="wordmark__mark"></span>
      <div class="wordmark__text">
        <span class="wordmark__name">Lumen Frame</span>
        <span class="wordmark__tagline">Architecture Corporate Commercial</span>
      </div>
    </div>

    <div class="person">
      <p class="person__name">Reid Calder</p>
      <p class="person__role">Photographer</p>
    </div>

    <ul class="contact-list">
      <li><svg viewBox="0 0 10 10"><path d="M1 3.5C1 2 2 1 3 1h4c1 0 2 1 2 2.5L7.5 4 7 3H3L2.5 4zM2.5 5h5L9 9H1z"/></svg>0412555018</li>
      <li><svg viewBox="0 0 10 10"><path d="M0.5 2h9v6h-9z M1 2.4l4 3 4-3" stroke="#fff" stroke-width="0.8"/></svg>hello@lumenframe.com.au</li>
      <li><svg viewBox="0 0 10 10"><circle cx="5" cy="5" r="4.5"/><path d="M0.5 5h9M5 0.5v9M2 2.5c2 1 4 1 6 0M2 7.5c2-1 4-1 6 0" stroke="#fff" stroke-width="0.6" fill="none"/></svg>www.lumenframe.com.au</li>
    </ul>

    <svg class="gold-band" viewBox="0 0 484 40" preserveAspectRatio="none" aria-hidden="true">
      <defs>
        <linearGradient id="goldSheen" x1="0" x2="1" y1="0" y2="0">
          <stop offset="0" stop-color="#8f6b2c"/>
          <stop offset="0.45" stop-color="#d7b468"/>
          <stop offset="0.75" stop-color="#b8914a"/>
          <stop offset="1" stop-color="#e0c37f"/>
        </linearGradient>
      </defs>
      <rect x="0" y="26" width="484" height="14" fill="url(#goldSheen)"/>
      <path d="M198 40 L222 4 Q224 1 228 1 H484 V40 Z" fill="url(#goldSheen)"/>
    </svg>
    <p class="address">48 Harbour Rd Lorne Vic 3232</p>
  </section>

</div>
</body>
</html>
```